WordPress Website Design for Multi-Brand Aviation Group (Unified Branding System)

Project Overview:
We are seeking a professional, modern WordPress website design for an aviation-focused umbrella company that owns and operates multiple subsidiary businesses. The goal is to create a cohesive visual system that clearly communicates that each company operates under the same parent organization, while still allowing each brand to maintain a slightly distinct identity.
This is not just a single website design—we are looking for a scalable design framework that can be applied across multiple aviation-related businesses.
Objectives:
- Establish a consistent, recognizable brand identity across all company websites
Clearly communicate the relationship between the parent company and its subsidiaries
-bCreate a clean, high-end corporate aviation aesthetic
- Ensure all designs are SEO-friendly and optimized for performance
- Allow flexibility for future expansion (additional subsidiaries)
- Target Audience:
- Corporate aviation clients
- Charter customers
- Students wishing to receive flight training
- Aircraft owners and operators
- Turbine aircraft training to meet insurance requirements
- Business professionals and high-net-worth individuals
- Aviation industry partners
Design Direction & Style:
We are looking for a premium, professional aviation feel—think clean, modern, and high-trust. The design should reflect the standards of corporate aviation: precision, safety, and sophistication.
Key style notes:
Minimalist but impactful layout
High-quality aviation photography (jets, interiors, operations, global travel)
Subtle motion/interaction (hover effects, transitions)
Clear typography hierarchy for readability and professionalism
Branding Requirements:
Incorporate the primary colors of the parent company logo across all designs
Website Structure (Core Pages):
Design a system that includes:
Home Page with the following links:
- About / Company Overview
- Aircraft Management
- Aircraft Acquisition
- Charter
- Pilot Services
- Trip Support
- Contact Page
Site should further include:
- Mobile-first responsive design
- Fast-loading, performance-optimized layouts
SEO & Technical Considerations:
- Design should support high-level SEO implementation:
- Clean layout structure that translates well to semantic HTML
- Proper heading hierarchy (H1, H2, H3)
- Space for keyword-rich content without clutter
- Optimized image placement (with alt text capability)
- Fast load times (lightweight design approach)
- Compatibility with WordPress SEO plugins (e.g., Yoast or Rank Math)
WordPress Requirements:
- Design should be easily built using WordPress (preferred builders: Elementor, Gutenberg, or similar)
- Reusable templates for scalability across multiple sites
- Easy for non-developers to update text and images
- Modular components (blocks/sections that can be reused across pages and sites)
- Navigation & UX:
- Simple, intuitive navigation
- Sticky header preferred
Style guide including:
- Colors
- Fonts
- Button styles
- Layout system
- Designs similar to high-end corporate aviation, private jet charter, or luxury service brands are preferred—clean, sharp, and premium without being overly flashy.
What We Want to Avoid:
- Overly busy layouts
- Generic templates with no brand identity
- Outdated or “stock” looking aviation designs
- Poor mobile responsiveness
Additional Notes:
We are building a long-term brand system, not just a one-off website. There is potential for ongoing work as we expand additional subsidiary sites.
We value designers who understand branding consistency across multiple business units and can create a scalable, professional system.
Include the attached main company logo "Vireton Aviation Group" and the "Member PJFO" logo on the main page.

```html
<!DOCTYPE html>
<html lang="en">
<head>
<meta charset="utf-8">
<title>Vireton Aviation Group</title>
<link rel="stylesheet" href="https://fonts.googleapis.com/css2?family=Krona+One&family=Lato:wght@400;700;900&display=swap">
<style>
:root{
  --blue:#0a5cb4;
  --blue-dark:#084f9c;
  --ink:#111111;
  --text:#2a2a2a;
  --muted:#555555;
  --white:#ffffff;
}
*{box-sizing:border-box;margin:0;padding:0}
html,body{width:1200px;height:2944px;overflow:hidden}
body{position:relative;background:var(--white);font-family:"Lato",sans-serif;color:var(--text)}
.abs{position:absolute}
.btn{position:absolute;display:flex;align-items:center;justify-content:center;border-radius:24px;background:var(--blue);color:var(--white);font-weight:700;font-size:15px;text-decoration:none}
.display{font-family:"Krona One",sans-serif;color:var(--ink);letter-spacing:1px}
.display .accent{color:var(--blue)}
.center{text-align:center}

/* header */
.site-header{position:absolute;left:0;top:0;width:1200px;height:104px;background:var(--white);z-index:2}
.brand{position:absolute;left:143px;top:28px;color:var(--blue);font-weight:900;line-height:1}
.brand .b1{font-size:31px;letter-spacing:3px;display:block}
.brand .b2{font-size:12px;letter-spacing:2.5px;display:block;margin-top:4px;color:var(--ink)}
.phone{position:absolute;left:641px;top:22px;display:flex;align-items:center;gap:12px;font-size:14px}
.icon-dot{width:24px;height:24px;border-radius:50%;background:var(--blue);display:flex;align-items:center;justify-content:center;flex:none}
.nav a{position:absolute;top:72px;font-size:14.5px;color:var(--ink);text-decoration:none}
.nav a.active{color:var(--blue)}

/* hero */
.hero-photo{position:absolute;left:0;top:104px;width:1200px;height:600px;
  background:
    radial-gradient(ellipse 420px 160px at 760px 470px,rgba(255,255,255,.85),rgba(255,255,255,0) 70%),
    radial-gradient(ellipse 380px 140px at 1080px 560px,rgba(255,255,255,.8),rgba(255,255,255,0) 70%),
    radial-gradient(ellipse 460px 200px at 180px 560px,rgba(250,251,252,.9),rgba(255,255,255,0) 70%),
    radial-gradient(ellipse 300px 140px at 900px 280px,rgba(95,100,110,.55),rgba(95,100,110,0) 70%),
    radial-gradient(ellipse 500px 220px at 1000px 120px,rgba(190,198,208,.7),rgba(190,198,208,0) 70%),
    linear-gradient(180deg,#c9d0d8 0%,#dfe3e8 35%,#cfd5dc 65%,#b9c0c9 100%)}
.hero-title{position:absolute;left:143px;top:234px;font-size:44px;line-height:72px}

/* about */
.about-photo{position:absolute;left:135px;top:720px;width:464px;height:464px;border-radius:50%;
  background:
    radial-gradient(ellipse 200px 120px at 230px 250px,rgba(245,246,248,.95),rgba(245,246,248,0) 70%),
    radial-gradient(ellipse 120px 70px at 190px 430px,rgba(20,60,110,.9),rgba(20,60,110,0) 70%),
    linear-gradient(180deg,#7f8892 0%,#a9b0b8 30%,#d7dbe0 55%,#9aa2ab 80%,#2c3440 100%);
  border-left:7px solid var(--blue);border-bottom:7px solid var(--blue)}
.about-title{position:absolute;left:652px;top:786px;width:420px;font-size:31px;line-height:48px}
.about-text{position:absolute;left:667px;top:897px;width:390px;font-size:13.6px;line-height:23px;color:var(--muted)}

/* services */
.section-title{position:absolute;left:0;width:1200px;font-size:31px}
.lead{position:absolute;left:190px;width:820px;font-size:17px;line-height:29px;color:var(--text)}
.card-label{position:absolute;background:var(--white);box-shadow:0 2px 10px rgba(0,0,0,.08);display:flex;align-items:center;justify-content:center}
.card-label span{font-size:17px;color:var(--ink);white-space:nowrap}
.photo{position:absolute}
.feature-card{position:absolute;left:631px;top:1398px;width:232px;height:294px;background:var(--blue);color:var(--white);padding:28px 16px 0 23px}
.feature-card h3{font-size:18px;font-weight:700;margin-bottom:16px}
.feature-card p{font-size:13.4px;line-height:23px}
.feature-card .more{display:flex;align-items:center;gap:12px;margin-top:20px;margin-left:5px;font-weight:700;font-size:15px}
.arrow-btn{position:absolute;width:36px;height:36px;border-radius:50%;border:1px solid #bbb;background:var(--white);display:flex;align-items:center;justify-content:center}

/* values */
.value{position:absolute;width:260px;text-align:center;color:var(--white)}
.value .ring{width:108px;height:108px;margin:0 auto;border-radius:50%;border:2px dashed rgba(255,255,255,.8);display:flex;align-items:center;justify-content:center}
.value .ring-in{width:96px;height:96px;border-radius:50%;background:var(--white);display:flex;align-items:center;justify-content:center}
.value h3{font-size:18px;font-weight:400;margin-top:22px;letter-spacing:.5px}
.value p{font-size:13.6px;line-height:23px;margin-top:6px}

/* footer */
.footer-brand{position:absolute;left:143px;top:2740px;color:var(--white);font-weight:900;line-height:1}
.footer-brand .b1{font-size:32px;letter-spacing:3px;display:block}
.footer-brand .b2{font-size:13px;letter-spacing:2.5px;display:block;margin-top:5px}
.social{position:absolute;width:27px;height:27px;border-radius:50%;border:1px solid var(--white)}
.social.on{background:var(--blue);border-color:var(--blue)}
.f-head{position:absolute;top:2692px;color:var(--white);font-size:18px;font-weight:700}
.f-list{position:absolute;left:419px;top:2734px;list-style:none;color:var(--white);font-size:14px;line-height:24px}
.f-contact{position:absolute;left:601px;display:flex;gap:13px;color:var(--white);font-size:14px;line-height:21px}
.member-badge{position:absolute;left:851px;top:2734px;width:204px;height:74px;background:var(--white);border-radius:4px;display:flex;align-items:center;justify-content:center}
.copyright{position:absolute;left:0;top:2910px;width:1200px;text-align:center;color:var(--white);font-size:14px}
</style>
</head>
<body>

<header class="site-header">
  <div class="brand"><span class="b1">VIRETON</span><span class="b2">AVIATION GROUP</span></div>
  <div class="phone"><span class="icon-dot"><svg width="12" height="12" viewBox="0 0 24 24"><path fill="#fff" d="M6.6 10.8a15 15 0 0 0 6.6 6.6l2.2-2.2c.3-.3.7-.4 1-.2 1.1.4 2.3.6 3.6.6.6 0 1 .4 1 1V20c0 .6-.4 1-1 1A17 17 0 0 1 3 4c0-.6.4-1 1-1h3.5c.6 0 1 .4 1 1 0 1.3.2 2.5.6 3.6.1.3 0 .7-.2 1z"/></svg></span>+1-888-888-8888</div>
  <a class="btn" style="left:823px;top:15px;width:232px;height:39px">Request Consultation</a>
  <nav class="nav">
    <a class="active" style="left:428px">HOME</a>
    <a style="left:523px">ABOUT</a>
    <a style="left:622px">SERVICES <svg width="9" height="6" viewBox="0 0 10 6"><path d="M1 1l4 4 4-4" stroke="#111" fill="none" stroke-width="1.5"/></svg></a>
    <a style="left:752px">CHARTER</a>
    <a style="left:868px">TRAINING</a>
    <a style="left:987px">CONTACT</a>
  </nav>
</header>

<section class="hero">
  <div class="hero-photo" role="img" aria-label="Jet fighter flying above white clouds"></div>
  <svg class="abs" style="left:0;top:590px" width="1200" height="125" viewBox="0 0 1200 125">
    <polygon points="0,85 1200,10 1200,125 0,125" fill="#fff"/>
    <polygon points="0,85 1200,10 1200,22 0,110" fill="var(--blue)"/>
  </svg>
  <h1 class="display hero-title"><span class="accent">ONE PLATFORM</span><br>TOTAL AVIATION<br>SOLUTIONS</h1>
  <a class="btn" style="left:143px;top:482px;width:208px;height:47px;font-size:16px">Explore Services</a>
</section>

<section class="about">
  <div class="about-photo" role="img" aria-label="Three pilots reviewing a laptop in an aircraft hangar"></div>
  <h2 class="display about-title center"><span class="accent">ABOUT</span> VIRETON<br>AVIATION</h2>
  <p class="about-text center">Sed ut perspiciatis unde omnis iste natus error sit voluptatem accusantium doloremque laudantium, totam rem aperiam, eaque ipsa quae ab illo inventore veritatis et quasi architecto beatae vitae dicta sunt explicabo. Nemo enim ipsam voluptatem quia voluptas sit aspernatur aut odit aut fugit,</p>
  <a class="btn" style="left:786px;top:1056px;width:151px;height:43px">Learn More</a>
</section>

<section class="services">
  <h2 class="display section-title center" style="top:1253px"><span class="accent">OUR</span> SERVICES</h2>
  <p class="lead center" style="top:1309px">Nemo enim ipsam voluptatem quia voluptas sit aspernatur aut odit aut fugit, sed quia consequuntur magni dolores eos qui ratione voluptatem sequi nesciunt.</p>

  <div class="arrow-btn" style="left:80px;top:1527px"><svg width="10" height="14" viewBox="0 0 10 14"><path d="M7 1L2 7l5 6" stroke="#111" fill="none" stroke-width="2"/></svg></div>
  <div class="arrow-btn" style="left:1083px;top:1527px"><svg width="10" height="14" viewBox="0 0 10 14"><path d="M3 1l5 6-5 6" stroke="#111" fill="none" stroke-width="2"/></svg></div>

  <div class="card-label" style="left:143px;top:1425px;width:57px;height:240px"><span style="transform:rotate(-90deg)">Pilot Services</span></div>
  <div class="photo" style="left:200px;top:1425px;width:138px;height:240px;background:radial-gradient(ellipse 70px 110px at 80px 170px,#e9edf2,rgba(233,237,242,0) 75%),linear-gradient(135deg,#d8dde2,#9aa5b1 60%,#6e7a88)" role="img" aria-label="Pilot with headset in a cockpit"></div>
  <div class="photo" style="left:338px;top:1413px;width:293px;height:264px;background:radial-gradient(ellipse 160px 60px at 146px 40px,#e4e6ea,rgba(228,230,234,0) 75%),linear-gradient(180deg,#c4c9cf 0%,#3a4c7a 35%,#2a3a66 70%,#8d939c 100%)" role="img" aria-label="Flight crew walking through an airport terminal"></div>
  <article class="feature-card">
    <h3>Aircraft Management</h3>
    <p>Lorem ipsum dolor sit amet, consectetur adipiscing elit, sed do eiusmod tempor incididunt ut labore et dolore magna aliqua. Ut enim ad minim veniam, quis nostrud exercitation</p>
    <div class="more">Learn More <svg width="18" height="12" viewBox="0 0 18 12"><path d="M1 6h15M11 1l5 5-5 5" stroke="#fff" fill="none" stroke-width="1.8"/></svg></div>
  </article>
  <div class="photo" style="left:863px;top:1425px;width:137px;height:240px;background:linear-gradient(180deg,#ece9e3 0%,#7387a3 40%,#4f6384 65%,#9a7450 100%)" role="img" aria-label="Business traveler working in a private jet cabin"></div>
  <div class="card-label" style="left:1000px;top:1425px;width:55px;height:240px"><span style="transform:rotate(90deg)">Aircraft Acquisition</span></div>
</section>

<section class="values">
  <svg class="abs" style="left:0;top:1730px" width="1200" height="600" viewBox="0 0 1200 600">
    <polygon points="0,100 1200,8 1200,520 0,592" fill="var(--ink)"/>
    <polygon points="0,104 1200,30 1200,496 0,570" fill="var(--blue)"/>
  </svg>
  <div class="value" style="left:133px;top:1868px">
    <div class="ring"><div class="ring-in"><svg width="62" height="62" viewBox="0 0 64 64" fill="none" stroke="var(--blue)" stroke-width="2.5"><circle cx="32" cy="32" r="22"/><circle cx="32" cy="32" r="12"/><path d="M32 4v12M32 48v12M4 32h12M48 32h12M26 32l4 4 8-8"/></svg></div></div>
    <h3>PRECISION</h3>
    <p>Sed ut perspiciatis unde omnis iste natus error sit voluptatem accusantium doloremque laudantium</p>
  </div>
  <div class="value" style="left:470px;top:1868px">
    <div class="ring"><div class="ring-in"><svg width="62" height="62" viewBox="0 0 64 64" fill="none" stroke="var(--blue)" stroke-width="2.5"><path d="M32 6l20 8v16c0 14-9 24-20 28-11-4-20-14-20-28V14z"/><path d="M22 36l20-12M30 30l-8-6M34 34l2 10"/></svg></div></div>
    <h3>SAFETY</h3>
    <p>Sed ut perspiciatis unde omnis iste natus error sit voluptatem accusantium doloremque laudantium</p>
  </div>
  <div class="value" style="left:807px;top:1868px">
    <div class="ring"><div class="ring-in"><svg width="62" height="62" viewBox="0 0 64 64" fill="none" stroke="var(--blue)" stroke-width="2.5"><circle cx="32" cy="32" r="22"/><path d="M18 26h18v-6l12 12-12 12v-6H18zM22 26v12M26 26v12"/></svg></div></div>
    <h3>SOPHISTICATION</h3>
    <p>Sed ut perspiciatis unde omnis iste natus error sit voluptatem accusantium doloremque laudantium</p>
  </div>
  <a class="btn" style="left:496px;top:2140px;width:208px;height:43px;background:var(--white);color:var(--blue);font-weight:400">Request Consultation</a>
</section>

<section class="cta">
  <h2 class="display section-title center" style="top:2356px">ELEVATE <span class="accent">YOUR AVIATION</span> STRATEGY</h2>
  <p class="lead center" style="top:2415px">Nemo enim ipsam voluptatem quia voluptas sit aspernatur aut odit aut fugit, sed quia consequuntur magni dolores eos qui ratione voluptatem sequi nesciunt.</p>
  <a class="btn" style="left:524px;top:2512px;width:152px;height:44px">Contact Us</a>
</section>

<footer class="site-footer">
  <svg class="abs" style="left:0;top:2568px" width="1200" height="376" viewBox="0 0 1200 376">
    <polygon points="0,100 1200,14 1200,376 0,376" fill="var(--ink)"/>
    <polygon points="0,100 1200,4 1200,18 0,106" fill="var(--blue)"/>
  </svg>
  <div class="footer-brand"><span class="b1">VIRETON</span><span class="b2">AVIATION GROUP</span></div>
  <span class="social" style="left:176px;top:2813px" role="img" aria-label="Social profile"></span>
  <span class="social on" style="left:212px;top:2813px" role="img" aria-label="Video channel"></span>
  <span class="social" style="left:247px;top:2813px" role="img" aria-label="Photo profile"></span>
  <span class="social" style="left:282px;top:2813px" role="img" aria-label="Short posts profile"></span>

  <h4 class="f-head" style="left:419px">Services</h4>
  <ul class="f-list">
    <li>Aircraft Management</li><li>Aircraft Acquisition</li><li>Charter</li><li>Pilot Services</li><li>Trip Support</li>
  </ul>

  <h4 class="f-head" style="left:599px">Contact details</h4>
  <div class="f-contact" style="top:2737px"><span class="icon-dot"><svg width="11" height="11" viewBox="0 0 24 24"><path fill="#fff" d="M6.6 10.8a15 15 0 0 0 6.6 6.6l2.2-2.2c.3-.3.7-.4 1-.2 1.1.4 2.3.6 3.6.6.6 0 1 .4 1 1V20c0 .6-.4 1-1 1A17 17 0 0 1 3 4c0-.6.4-1 1-1h3.5c.6 0 1 .4 1 1 0 1.3.2 2.5.6 3.6.1.3 0 .7-.2 1z"/></svg></span><span style="padding-top:2px">+1-888-888-8888</span></div>
  <div class="f-contact" style="top:2778px"><span class="icon-dot"><svg width="11" height="9" viewBox="0 0 22 16"><rect x="1" y="1" width="20" height="14" rx="1" fill="#fff"/><path d="M1 2l10 7 10-7" stroke="var(--blue)" fill="none" stroke-width="1.8"/></svg></span><span style="padding-top:2px">info@viretonaviation.com</span></div>
  <div class="f-contact" style="top:2819px"><span class="icon-dot"><svg width="10" height="12" viewBox="0 0 20 26"><path fill="#fff" d="M10 0a9 9 0 0 0-9 9c0 7 9 17 9 17s9-10 9-17a9 9 0 0 0-9-9zm0 12a3 3 0 1 1 0-6 3 3 0 0 1 0 6z"/></svg></span><span style="padding-top:2px">123 Lorem ipsum dolorye<br>Florida 45678 USA</span></div>

  <h4 class="f-head" style="left:851px">Our Member</h4>
  <div class="member-badge" role="img" aria-label="Member PJFO badge"><span style="display:block;width:150px;height:36px;border-radius:4px;background:#e6ebf2"></span></div>

  <p class="copyright">© 2026 Copyright Vireton Aviation.</p>
</footer>

</body>
</html>
```